Nutrition business needs logo & business card design

We need a business card & logo design for a new company based in Toronto, Ontario Canada called Verdel Wellworks.

We provide nutrition service using metrics as guide to manage client's progress. Our service creates individualized nutrition and lifestyle strategies that focuses on improving Performance, Longevity and Weight Loss. I would like to see designs that use the color of green, gray, blue and white.

The final design should:

--convey a feeling of connectedness with positive transformation.

-- communicate the idea of awareness with guided effort that yields personal independence for a better and more productive life

Target Market(s)

Professionals who work in the IT/Computer/Engineering/Banking industry specifically Directors, Managers, CEO's.

Industry/Entity Type

Health And Wellness

Contact Information for Business Card

Dorvane Pike, Owner
email: DPIKE@verdelwellworks.example
tel: - 555-204-7718

Logo Text

better health through analytics or measure to manage

Font styles to use
Other font styles liked:
• Garamound

Colors
ffffff
abd037
85acd3
757575
34a7d7

Requirements
Must have
• Good contrast and decent size font - ease of readability, aesthetically nice colors
Nice to have
• image of chart or graph that conveys measurement or analytics
Should not have
• Borders, images of food,

```html
<!DOCTYPE html>
<html lang="en">
<head>
<meta charset="utf-8">
<title>Verdel Wellworks – Business Card</title>
<link rel="stylesheet" href="https://fonts.googleapis.com/css2?family=Lato:wght@400;700&family=Open+Sans:wght@400;600&display=swap">
<style>
  :root {
    --stage: #000000;
    --card: #333437;
    --card-edge: #3a3b3e;
    --divider: #424347;
    --green: #3fae29;
    --blue: #1e8cf0;
    --text: #ffffff;
  }
  html, body {
    margin: 0;
    padding: 0;
    width: 1200px;
    height: 900px;
    overflow: hidden;
    background: var(--stage);
  }
  .canvas {
    position: relative;
    width: 1200px;
    height: 900px;
    background: var(--stage);
    font-family: "Open Sans", Arial, sans-serif;
  }
  .card {
    position: absolute;
    top: 271px;
    width: 457px;
    height: 281px;
    border-radius: 14px;
    background: var(--card);
    box-shadow: inset 0 0 0 1px var(--card-edge);
  }
  .card--front { left: 137px; }
  .card--back { left: 626px; }

  .brand-mark {
    position: absolute;
    left: 50px;
    top: 66px;
    width: 144px;
    height: 144px;
  }
  .brand-mark__name {
    position: absolute;
    inset: 0;
    display: flex;
    align-items: center;
    justify-content: center;
    text-align: center;
    font-family: "Lato", Arial, sans-serif;
    font-size: 19px;
    line-height: 1.2;
    color: var(--green);
  }
  .divider {
    position: absolute;
    left: 218px;
    top: 74px;
    width: 1px;
    height: 136px;
    background: var(--divider);
  }
  .contact {
    position: absolute;
    left: 250px;
    top: 64px;
    color: var(--text);
    font-size: 12.5px;
    line-height: 17px;
  }
  .contact__name {
    margin: 0;
    font-size: 18.5px;
    line-height: 22px;
    font-weight: 400;
  }
  .contact__first { color: var(--green); }
  .contact__last { color: var(--blue); }
  .contact__role { margin: 0 0 9px; }
  .contact__address { margin: 0 0 9px; font-style: normal; }
  .contact__list { list-style: none; margin: 0; padding: 0; }
  .contact__list li { display: flex; align-items: center; gap: 6px; height: 16.5px; }
  .contact__icon { width: 10px; height: 10px; fill: var(--green); flex: none; }

  .back-ring {
    position: absolute;
    left: 169px;
    top: 62px;
    width: 110px;
    height: 110px;
  }
  .wordmark {
    position: absolute;
    left: 0;
    right: 0;
    top: 178px;
    margin: 0;
    text-align: center;
    font-family: "Lato", Arial, sans-serif;
    font-weight: 400;
    font-size: 33px;
    letter-spacing: -0.5px;
    color: var(--blue);
  }
</style>
</head>
<body>
<main class="canvas">
  <section class="card card--front" aria-label="Business card front">
    <div class="brand-mark">
      <svg viewBox="0 0 144 144" width="144" height="144" aria-hidden="true">
        <circle cx="72" cy="72" r="68" fill="none" stroke="var(--blue)" stroke-width="5"/>
      </svg>
      <span class="brand-mark__name">Verdel<br>Wellworks</span>
    </div>
    <div class="divider"></div>
    <div class="contact">
      <h1 class="contact__name"><span class="contact__first">Dorvane</span> <span class="contact__last">Pike</span></h1>
      <p class="contact__role">Managing Director</p>
      <address class="contact__address">12345, Address Goes Here<br>Country Name, 123456.</address>
      <ul class="contact__list">
        <li>
          <svg class="contact__icon" viewBox="0 0 10 10"><path d="M2 0.5 L3.6 2.8 L2.7 3.8 C3.3 5 4.9 6.6 6.2 7.3 L7.2 6.4 L9.5 8 L8.3 9.5 C4.5 9.3 0.7 5.5 0.5 1.7 Z"/></svg>
          <span>555-204-7718</span>
        </li>
        <li>
          <svg class="contact__icon" viewBox="0 0 10 10"><path d="M0.5 2 H9.5 V8.5 H0.5 Z M0.5 2 L5 5.5 L9.5 2" fill="var(--green)" stroke="var(--card)" stroke-width="0.8"/></svg>
          <span>info@verdelwellworks.example</span>
        </li>
        <li>
          <svg class="contact__icon" viewBox="0 0 10 10"><path d="M4 6 L6 4 M3.2 4.6 L1.6 6.2 A1.6 1.6 0 0 0 3.8 8.4 L5.4 6.8 M4.6 3.2 L6.2 1.6 A1.6 1.6 0 0 1 8.4 3.8 L6.8 5.4" fill="none" stroke="var(--green)" stroke-width="1.3" stroke-linecap="round"/></svg>
          <span>www.verdelwellworks.example</span>
        </li>
      </ul>
    </div>
  </section>

  <section class="card card--back" aria-label="Business card back">
    <svg class="back-ring" viewBox="0 0 110 110" aria-hidden="true">
      <circle cx="55" cy="55" r="52" fill="none" stroke="var(--green)" stroke-width="4"/>
    </svg>
    <h2 class="wordmark">Verdel Wellworks</h2>
  </section>
</main>
</body>
</html>
```